Website Design for a holiday home letting busines

We require a redesign of our present website www.pinebrookstays.com. We want the website to stand out and look professional and clean to make holiday hunters want to book a caravan or lodge holiday with us. Our logo is red however we DO NOT want the website to be red. We want a natural colour scheme.

The final design should communicate that we are a professional company to book with.

On the home page we require;
Overview of company
Photo
Search box for holiday (check in)
Late Deals
Reviews
News

We would like the following pages designed; home page, available dates page, caravans page, content page.

The website should be responsive for smart phones. One website I do like is http://www.verdoliso.be/nl/

Target Market(s)

Families

Industry/Entity Type

Travel

Number of Pages Required

5+ page

Font styles to use
Serif

Requirements
Must have
• The project must be responsive for mobile phones and tablets.
• Ability to search for holiday home holidays
• We want a natural colour scheme.
Nice to have
• A style we like is http://www.verdoliso.be/nl/
Should not have
• Do not use red as a colour for the website. Our logo is red so this is the only time we want this used.

```html
<!DOCTYPE html>
<html lang="en">
<head>
<meta charset="utf-8">
<title>Pinebrook Stays – Private Holiday Rentals</title>
<link href="https://fonts.googleapis.com/css2?family=Raleway:wght@400;600;700&family=Open+Sans:wght@400;600&display=swap" rel="stylesheet">
<style>
:root{
  --forest:#0f5f58;
  --pine:#17796f;
  --moss:#2f8c7f;
  --sage:#8fbfb5;
  --stone:#eef3f1;
  --paper:#ffffff;
  --ink:#23403c;
  --muted:#6f8a86;
  --footer:#1d4a45;
  --footer-line:#2f625c;
  --veil:rgba(22,132,121,.78);
}
*{box-sizing:border-box;margin:0;padding:0}
html,body{width:1200px;height:2936px;overflow:hidden}
body{position:relative;background:var(--paper);font-family:"Open Sans",Arial,sans-serif;color:var(--ink);font-size:13px}
h1,h2,h3,h4{font-family:"Raleway",Arial,sans-serif}
.abs{position:absolute}

/* header */
.site-header{position:absolute;left:0;top:0;width:1200px;height:120px;background:var(--forest)}
.brand{position:absolute;left:100px;top:30px;display:flex;align-items:center;gap:12px;color:#fff;font-family:"Raleway",sans-serif;font-weight:700;font-size:26px}
.brand-dot{width:50px;height:50px;border-radius:50%;background:var(--sage)}
.header-contact{position:absolute;top:46px;display:flex;align-items:center;gap:8px;color:#dcebe8;font-size:13px}
.header-contact svg{width:22px;height:22px}
.btn-book{position:absolute;right:100px;top:40px;width:150px;height:38px;background:var(--moss);color:#fff;border:1px solid #4aa698;font-family:"Raleway",sans-serif;font-weight:600;font-size:13px;display:flex;align-items:center;justify-content:center;letter-spacing:.05em}
.main-nav{position:absolute;left:0;top:120px;width:1200px;height:32px;background:var(--pine);display:flex;justify-content:center;gap:46px;align-items:center}
.main-nav a{color:#fff;text-decoration:none;font-size:12px;font-family:"Raleway",sans-serif;font-weight:600}

/* hero */
.hero{position:absolute;left:0;top:152px;width:1200px;height:500px;background:linear-gradient(120deg,#5a6f66,#889a8c 45%,#b8c3b5)}
.hero-copy{position:absolute;left:640px;top:120px;width:440px;color:#fff}
.hero-copy h1{font-size:40px;font-weight:600}
.hero-copy p{margin-top:10px;font-size:14px;line-height:1.6}
.search-bar{position:absolute;left:200px;top:620px;width:800px;height:40px;background:rgba(255,255,255,.95);display:flex}
.search-field{flex:1;border-right:1px solid #d7e1de;padding:0 14px;display:flex;align-items:center;justify-content:space-between;color:var(--muted);font-size:12px}
.search-btn{width:130px;background:var(--moss);color:#fff;display:flex;align-items:center;justify-content:center;font-weight:600;font-size:12px;letter-spacing:.05em}

/* welcome */
.welcome-photo{position:absolute;left:100px;top:720px;width:340px;height:230px;background:linear-gradient(160deg,#8fb3c4,#a9b79c 60%,#6f8a5e)}
.welcome-text{position:absolute;left:480px;top:720px;width:620px}
.welcome-text h2{font-size:28px;font-weight:600;color:var(--pine)}
.welcome-text p{margin-top:14px;line-height:1.75;color:var(--muted);font-size:13px}
.btn-outline{display:inline-block;margin-top:22px;padding:12px 30px;background:var(--moss);color:#fff;font-weight:600;font-size:12px}

/* section titles */
.section-title{position:absolute;left:0;width:1200px;text-align:center;font-size:22px;font-weight:700;color:var(--forest);letter-spacing:.04em}

/* cards */
.card-row{position:absolute;left:100px;width:1000px;display:flex;gap:20px}
.card{width:235px;height:280px;background:var(--paper);border:1px solid #d6e2df}
.card-photo{height:160px;position:relative}
.card-body{padding:10px 12px;font-size:11px;color:var(--muted);line-height:1.5}
.card-body h4{color:var(--pine);font-size:13px;margin:4px 0;font-weight:700}
.card-meta{display:flex;justify-content:space-between;border-top:1px solid #e0e8e6;margin-top:10px;padding-top:8px}
.price-badge{position:absolute;right:10px;bottom:-20px;width:56px;height:56px;border-radius:50%;background:var(--moss);border:3px solid #fff;color:#fff;font-size:11px;font-weight:700;display:flex;align-items:center;justify-content:center;text-align:center;line-height:1.1}
.p1{background:linear-gradient(135deg,#b9a88c,#e3d7c2)}
.p2{background:linear-gradient(135deg,#d9ded8,#a7b4ad)}
.p3{background:linear-gradient(135deg,#c9c0b0,#eeeae2)}
.p4{background:linear-gradient(135deg,#e6e8dd,#a0ad8f)}

/* reviews */
.reviews{position:absolute;left:0;top:1440px;width:1200px;height:270px;background:linear-gradient(90deg,#6c7a73,#9aa79c 50%,#75847a);color:#fff;text-align:center}
.reviews h3{margin-top:38px;font-size:22px;letter-spacing:.05em}
.reviews p{width:640px;margin:14px auto 0;font-size:13px;line-height:1.6}
.reviewer{width:70px;height:70px;border-radius:50%;background:#c9d2cb;border:3px solid #fff;margin:20px auto 0}
.reviewer-name{font-size:12px;margin-top:6px}

/* news */
.col-title{position:absolute;font-size:20px;font-weight:700;color:var(--forest)}
.news-item{position:absolute;display:flex;gap:14px;width:330px}
.news-thumb{width:110px;height:80px;flex:none}
.news-item h4{font-size:12px;color:var(--pine)}
.news-item p{font-size:11px;color:var(--muted);line-height:1.5;margin-top:4px}
.social-box{position:absolute;left:810px;top:2310px;width:290px;height:280px;background:var(--stone);border:1px solid #d6e2df;padding:14px}
.social-head{display:flex;gap:10px;align-items:center}
.social-head .sq{width:38px;height:38px;background:var(--sage)}
.social-head b{font-family:"Raleway",sans-serif;color:var(--pine);font-size:14px}
.social-grid{display:grid;grid-template-columns:repeat(5,1fr);gap:6px;margin-top:120px}
.social-grid span{height:40px;background:#b9c9c3}

/* footer */
.site-footer{position:absolute;left:0;top:2640px;width:1200px;height:260px;background:var(--footer);color:#c9dcd8}
.footer-col{position:absolute;top:36px;width:220px;font-size:12px;line-height:2}
.footer-col h4{color:#fff;font-size:13px;letter-spacing:.06em;margin-bottom:10px}
.footer-col li{list-style:none}
.footer-input{height:30px;background:#fff;margin-top:10px}
.footer-btn{width:90px;height:28px;background:var(--moss);margin-top:8px;color:#fff;font-size:11px;display:flex;align-items:center;justify-content:center}
.social-link{display:flex;align-items:center;gap:10px}
.social-link i{display:inline-block;width:20px;height:20px;border-radius:50%;border:1px solid #8fb5ae}
.copyright{position:absolute;left:0;top:2900px;width:1200px;height:36px;background:#163d39;color:#9fbab5;font-size:11px;display:flex;align-items:center;justify-content:center}

/* subscribe overlay */
.veil{position:absolute;left:0;top:0;width:1200px;height:2936px;background:var(--veil)}
.subscribe{position:absolute;left:400px;top:252px;width:400px;height:300px;background:#fff;box-shadow:0 6px 24px rgba(0,0,0,.25);padding:22px 28px}
.subscribe-head{display:flex;align-items:center;gap:12px}
.subscribe-head .dot{width:40px;height:40px;border-radius:50%;background:var(--sage)}
.subscribe-head h3{font-size:20px;color:var(--forest)}
.subscribe p{font-size:11px;color:var(--muted);margin-top:10px;line-height:1.5}
.sub-input{height:32px;border:1px solid #cbd8d5;margin-top:12px;padding:0 10px;font-size:11px;color:#9aaca8;display:flex;align-items:center}
.sub-actions{display:flex;align-items:center;gap:20px;margin-top:16px}
.sub-btn{width:96px;height:32px;background:var(--pine);color:#fff;font-size:12px;font-weight:600;display:flex;align-items:center;justify-content:center}
.sub-link{font-size:11px;color:var(--pine);text-decoration:underline}
.sub-help{font-size:11px;color:var(--ink);margin-top:12px}
.sub-close{position:absolute;right:10px;top:10px;width:18px;height:18px}
</style>
</head>
<body>

<header class="site-header">
  <div class="brand"><span class="brand-dot"></span>Pinebrook Stays</div>
  <div class="header-contact" style="left:560px">
    <svg viewBox="0 0 24 24" fill="none" stroke="#dcebe8" stroke-width="1.6"><path d="M5 3h4l2 5-3 2a12 12 0 0 0 6 6l2-3 5 2v4a2 2 0 0 1-2 2A18 18 0 0 1 3 5a2 2 0 0 1 2-2z"/></svg>
    01632 960 418
  </div>
  <div class="header-contact" style="left:740px">
    <svg viewBox="0 0 24 24" fill="none" stroke="#dcebe8" stroke-width="1.6"><rect x="3" y="5" width="18" height="14"/><path d="M3 6l9 7 9-7"/></svg>
    hello@pinebrookstays.com
  </div>
  <div class="btn-book">BOOK NOW</div>
</header>

<nav class="main-nav">
  <a>Home</a><a>About</a><a>Caravans</a><a>Available Dates</a><a>Lodges</a><a>Late Deals</a><a>Reviews</a><a>Contact</a>
</nav>

<section class="hero" role="img" aria-label="Family relaxing on the decking of a holiday lodge">
  <div class="hero-copy">
    <h1>Private Holiday Rentals</h1>
    <p>Quiet lodges and caravans set in open countryside, ready for your next family break.</p>
  </div>
</section>

<form class="search-bar">
  <div class="search-field">Location <span>▾</span></div>
  <div class="search-field">Property type <span>▾</span></div>
  <div class="search-field">Check in <span>▾</span></div>
  <div class="search-field">Nights <span>▾</span></div>
  <div class="search-btn">SEARCH NOW</div>
</form>

<div class="welcome-photo" role="img" aria-label="Row of holiday lodges on a green lawn"></div>
<div class="welcome-text">
  <h2>Welcome to Pinebrook Stays</h2>
  <p>We are a family run letting business offering privately owned caravans and lodges across a choice of peaceful parks. Every home is checked, cleaned and ready for your arrival, with clear prices and friendly local support throughout your stay.</p>
  <p>Browse our homes, check live availability and book online in just a few minutes. Whether you want a short break or a long summer holiday, we have a place for you.</p>
  <span class="btn-outline">READ MORE</span>
</div>

<h2 class="section-title" style="top:1070px">OUR CARAVANS AND LODGES</h2>
<div class="card-row" style="top:1130px">
  <article class="card"><div class="card-photo p1" role="img" aria-label="Caravan lounge interior"></div><div class="card-body">Sleeps 6 · 3 bedrooms<h4>OAK MEADOW</h4>Spacious caravan with decking and park views.<div class="card-meta"><span>From £299</span><span>★ 4.8</span></div></div></article>
  <article class="card"><div class="card-photo p2" role="img" aria-label="Lodge kitchen interior"></div><div class="card-body">Sleeps 4 · 2 bedrooms<h4>THE WILLOWS</h4>Bright lodge with open plan kitchen area.<div class="card-meta"><span>From £349</span><span>★ 4.7</span></div></div></article>
  <article class="card"><div class="card-photo p3" role="img" aria-label="Caravan bedroom interior"></div><div class="card-body">Sleeps 6 · 3 bedrooms<h4>THE ELLISTON</h4>Modern caravan close to the park pool.<div class="card-meta"><span>From £279</span><span>★ 4.6</span></div></div></article>
  <article class="card"><div class="card-photo p4" role="img" aria-label="Lodge living room with flowers"></div><div class="card-body">Sleeps 8 · 4 bedrooms<h4>BIRCH HOLLOW</h4>Large family lodge with private hot tub.<div class="card-meta"><span>From £499</span><span>★ 4.9</span></div></div></article>
</div>

<section class="reviews" role="img" aria-label="Caravan living room background behind guest reviews">
  <h3>REVIEWS</h3>
  <p>“A lovely clean caravan in a quiet spot. The booking was simple and the children loved every minute. We will be back next summer.”</p>
  <div class="reviewer"></div>
  <div class="reviewer-name">Sarah, Leeds</div>
</section>

<h2 class="section-title" style="top:1750px">LATE DEALS</h2>
<div class="card-row" style="top:1810px">
  <article class="card"><div class="card-photo p1" role="img" aria-label="Caravan lounge"><span class="price-badge">£199</span></div><div class="card-body"><h4>THE CLOVER</h4>Friday 3 nights, sleeps 6, save 20%.<div class="card-meta"><span>Mar 14</span><span>3 nights</span></div></div></article>
  <article class="card"><div class="card-photo p2" role="img" aria-label="Lodge dining area"><span class="price-badge">£229</span></div><div class="card-body"><h4>THE ELLISTON</h4>Monday 4 nights, sleeps 6, save 15%.<div class="card-meta"><span>Mar 17</span><span>4 nights</span></div></div></article>
  <article class="card"><div class="card-photo p3" role="img" aria-label="Caravan bedroom"><span class="price-badge">£249</span></div><div class="card-body"><h4>THE CLOVER</h4>Friday 7 nights, sleeps 6, save 25%.<div class="card-meta"><span>Mar 21</span><span>7 nights</span></div></div></article>
  <article class="card"><div class="card-photo p4" role="img" aria-label="Lodge lounge"><span class="price-badge">£189</span></div><div class="card-body"><h4>THE CLOVER</h4>Monday 4 nights, sleeps 4, save 10%.<div class="card-meta"><span>Mar 24</span><span>4 nights</span></div></div></article>
</div>

<h3 class="col-title" style="left:100px;top:2300px">LATEST NEWS</h3>
<div class="news-item" style="left:100px;top:2350px"><div class="news-thumb p2" role="img" aria-label="Lodge exterior"></div><div><h4>New lodges for spring</h4><p>Three new lodges join our list this season.</p></div></div>
<div class="news-item" style="left:100px;top:2460px"><div class="news-thumb p4" role="img" aria-label="Park pathway"></div><div><h4>Park upgrades finished</h4><p>Fresh paths and a new play area for kids.</p></div></div>

<h3 class="col-title" style="left:460px;top:2300px">BLOG FEED</h3>
<div class="news-item" style="left:460px;top:2350px"><div class="news-thumb p1" role="img" aria-label="Caravan decking"></div><div><h4>Top days out nearby</h4><p>Our pick of family walks and beaches.</p></div></div>
<div class="news-item" style="left:460px;top:2460px"><div class="news-thumb p3" role="img" aria-label="Caravan interior"></div><div><h4>Packing for a break</h4><p>Simple tips for a stress free arrival.</p></div></div>

<aside class="social-box">
  <div class="social-head"><span class="sq"></span><div><b>Pinebrook Stays</b><br><span style="font-size:11px;color:var(--muted)">1,240 followers</span></div></div>
  <div class="social-grid"><span></span><span></span><span></span><span></span><span></span><span></span><span></span><span></span><span></span><span></span></div>
</aside>

<footer class="site-footer">
  <div class="footer-col" style="left:100px"><h4>USEFUL LINKS</h4><ul><li>Home</li><li>About us</li><li>Caravans</li><li>Lodges</li><li>Late deals</li><li>Contact</li></ul></div>
  <div class="footer-col" style="left:360px"><h4>CONTACT DETAILS</h4><ul><li>12 Meadow Lane, Dunmore</li><li>01632 960 418</li><li>hello@pinebrookstays.com</li><li>www.pinebrookstays.com</li></ul></div>
  <div class="footer-col" style="left:620px"><h4>NEWSLETTER SIGN UP</h4><div>Get late deals first.</div><div class="footer-input"></div><div class="footer-btn">SIGN UP</div></div>
  <div class="footer-col" style="left:900px"><h4>SOCIAL MEDIA LINKS</h4><ul><li class="social-link"><i></i>Social feed</li><li class="social-link"><i></i>Photo feed</li><li class="social-link"><i></i>Video channel</li><li class="social-link"><i></i>Newsfeed</li></ul></div>
</footer>
<div class="copyright">© 2024 Pinebrook Stays. All rights reserved.</div>

<div class="veil"></div>
<div class="subscribe">
  <svg class="sub-close" viewBox="0 0 18 18"><circle cx="9" cy="9" r="8" fill="none" stroke="#6f8a86"/><path d="M6 6l6 6M12 6l-6 6" stroke="#6f8a86" stroke-width="1.4"/></svg>
  <div class="subscribe-head"><span class="dot"></span><h3>SUBSCRIBE</h3></div>
  <p>Get our latest late deals and monthly news sent straight to your inbox.</p>
  <div class="sub-input">Enter your name here</div>
  <div class="sub-input">Enter your email here</div>
  <div class="sub-actions"><span class="sub-btn">Sign up</span><span class="sub-link">I already have an account</span></div>
  <div class="sub-help">Need help?</div>
</div>

</body>
</html>
```